Harbor Loom Floors Letterhead

Letterhead used for business reasons. It must be editable and easy to use.

Address is 2715 W. Pelican Lane Englewood FL 34187 - 941.382.6519

```html
<!DOCTYPE html>
<html lang="en">
<head>
<meta charset="utf-8">
<title>Harbor Loom Floors Letterhead</title>
<link rel="stylesheet" href="https://fonts.googleapis.com/css2?family=Source+Sans+3:wght@400;600&family=Montserrat:wght@400&display=swap">
<style>
  :root {
    --backdrop: #e4e4e4;
    --paper: #ffffff;
    --brand-orange: #e08c26;
    --ink-navy: #1c2747;
    --ink-body: #4a4a4a;
    --ink-footer: #2b2b2b;
    --signature-tone: #d9d9d9;
  }
  * { margin: 0; padding: 0; box-sizing: border-box; }
  html, body {
    width: 1200px; height: 1079px; overflow: hidden;
    background: var(--backdrop);
  }
  .letterhead {
    position: absolute; left: 245px; top: 37px;
    width: 710px; height: 1004px;
    background: var(--paper);
    box-shadow: 0 6px 22px rgba(0,0,0,0.18);
    font-family: "Source Sans 3", sans-serif;
  }
  .brand-name {
    position: absolute; left: 69px; top: 62px;
    font-weight: 600; font-size: 44px; line-height: 1;
    color: var(--brand-orange);
    letter-spacing: 0.2px;
  }
  .salutation {
    position: absolute; left: 69px; top: 298px;
    font-size: 17px; color: var(--ink-navy);
  }
  .letter-body {
    position: absolute; left: 70px; top: 355px; width: 570px;
  }
  .letter-body p {
    font-size: 12.2px; line-height: 14.3px;
    color: var(--ink-body);
    text-align: justify;
    margin-bottom: 28.5px;
  }
  .closing {
    position: absolute; left: 70px; top: 668px;
    font-size: 12.5px; color: var(--ink-body);
  }
  .signature {
    position: absolute; left: 70px; top: 688px;
    width: 62px; height: 8px; background: var(--signature-tone);
    border-radius: 2px;
  }
  .signer-name {
    position: absolute; left: 70px; top: 711px;
    font-size: 12.5px; color: var(--ink-body);
    text-transform: uppercase;
  }
  .footer {
    position: absolute; left: 217px; top: 910px; width: 274px;
    font-family: "Montserrat", sans-serif; color: var(--ink-footer);
    text-align: center;
  }
  .footer-phone {
    font-size: 12px; display: flex; align-items: center; justify-content: center; gap: 5px;
  }
  .footer-rule {
    height: 1.5px; background: var(--brand-orange); margin: 8px 0 7px;
  }
  .footer-address { font-size: 12px; }
</style>
</head>
<body>
  <main class="letterhead">
    <div class="brand-name">Harbor Loom Floors</div>

    <p class="salutation">Dear Mr. Ellison</p>

    <section class="letter-body">
      <p>Lorem Ipsum is simply dummy text of the printing and typesetting industry. Lorem Ipsum has been the industry's standard dummy text ever since the 1500s, when an unknown printer took a galley of type and scrambled it to make a type specimen book. It has survived not only five centuries, but also the leap into electronic typesetting, remaining essentially unchanged. It was popularised in the 1960s with the release of Letraset sheets containing Lorem Ipsum passages</p>
      <p>Lorem Ipsum is simply dummy text of the printing and typesetting industry. Lorem Ipsum has been the industry's standard dummy text ever since the 1500s, when an unknown printer took a galley of type and scrambled it to make a type specimen book. It has survived not only five centuries, but also the leap into electronic typesetting, remaining essentially unchanged. It was popularised in the 1960s with the release of Letraset sheets containing Lorem Ipsum passages</p>
      <p>Lorem Ipsum is simply dummy text of the printing and typesetting industry. Lorem Ipsum has been the industry's standard dummy text ever since the 1500s, when an unknown printer took a galley of type and scrambled it to make a type specimen book. It has survived not only five centuries, but also the leap into electronic typesetting, remaining essentially unchanged. It was popularised in the 1960s with the release of Letraset sheets containing Lorem Ipsum passages</p>
    </section>

    <p class="closing">Sincerely</p>
    <div class="signature" role="img" aria-label="Handwritten signature"></div>
    <p class="signer-name">Dana Whitcombe</p>

    <footer class="footer">
      <div class="footer-phone">
        <svg width="11" height="11" viewBox="0 0 24 24" aria-hidden="true">
          <path fill="var(--brand-orange)" d="M6.6 10.8a15.2 15.2 0 0 0 6.6 6.6l2.2-2.2a1 1 0 0 1 1-.25 11.4 11.4 0 0 0 3.6.57 1 1 0 0 1 1 1V20a1 1 0 0 1-1 1A17 17 0 0 1 3 4a1 1 0 0 1 1-1h3.5a1 1 0 0 1 1 1c0 1.25.2 2.45.57 3.57a1 1 0 0 1-.25 1z"/>
        </svg>
        <span>941.382.6519</span>
      </div>
      <div class="footer-rule"></div>
      <div class="footer-address">2715 W. Pelican Lane Englewood FL 34187</div>
    </footer>
  </main>
</body>
</html>
```